Commercial Real Estate for Lease Listing Flyer

I am looking to put together a flyer for our available office space in our building. It needs to look professional and it will be standard sized 8.5 x 11 and double sided. Full color as well. This flyer will need to be able to be put in a PDF and a picture file that can be embedded in an email. I have included pictures, logo, and a Word document with the information you should need. Also, I included a bunch of SAMPLE leasing flyers that you can get ideas from. The floor plan is also included in here. I want it specifically noted that the top suite is Suite 100 and the bottom suite is 120. And list their size as well. I will be reviewing all designs very quickly, so be sure to check the comments.

• Please refer to these links for additional photos:
• "Twilight 1.jpg" at: https://files.plinthdocs.net/a/preview/3f7d1a92-b4e0-4c1a-8e5f-71c0d2ab9e34
• Twilight 2_straightened.jpg" at: https://files.plinthdocs.net/a/preview/a15c8e03-7d2b-4f9e-b6a1-0c93e4f72d58
• "Twilight 3.jpg" at: https://files.plinthdocs.net/a/preview/6e2b9f71-c3a4-4d08-9e7b-5f1a8c03d6e2
• "Twilight 4.jpg" at: https://files.plinthdocs.net/a/preview/c84a0d6e-1f3b-4e57-a2c9-9b7e05f4d813
• "Twilight 5.jpg" at: https://files.plinthdocs.net/a/preview/7b0f5c28-e6d1-4a93-8f4e-d25a1b6c07f9
• "Twilight 6.jpg" at: https://files.plinthdocs.net/a/preview/e3c6a417-5b92-4f0d-bc8e-4a1f97d2e065
• "Twilight 7.jpg" at: https://files.plinthdocs.net/a/preview/5a9d2e80-c7f4-4b16-93a0-e8b6f1c4d27a
• "Twilight 8.jpg" at: https://files.plinthdocs.net/a/preview/b2e7f069-84c3-4d5a-a71e-3c0d9b58f6e4
• "Twilight 9.jpg" at: https://files.plinthdocs.net/a/preview/4d8c1b3f-a0e5-4f72-8b69-f17e2c05a9d3
• "Twilight 10.jpg" at: https://files.plinthdocs.net/a/preview/f09a6c52-3e18-4b7d-9c24-6b5d80e1f3a7
• "Twilight 11.jpg" at: https://files.plinthdocs.net/a/preview/8e4f2d06-b9c7-4a31-85e0-d7a3c16f4b92

```html
<!DOCTYPE html>
<html lang="en">
<head>
<meta charset="utf-8">
<title>Alder Road Centre – Office Space for Lease</title>
<link rel="stylesheet" href="https://fonts.googleapis.com/css2?family=Montserrat:wght@600;700;800&family=Open+Sans:ital,wght@0,400;0,600;0,700;1,700&display=swap">
<style>
  :root{
    --red:#e8363b;
    --dark:#2a2a2a;
    --ink:#1e1e1e;
    --paper:#e5e5e5;
    --white:#ffffff;
    --backdrop-a:#a6a6a6;
    --backdrop-b:#8f8f8f;
    --wood-a:#d8b77a;
    --wood-b:#6b4430;
    --plan:#f3f3f3;
  }
  *{box-sizing:border-box;margin:0;padding:0}
  html,body{width:1200px;height:1200px;overflow:hidden}
  body{background:radial-gradient(circle at 50% 40%,var(--backdrop-a),var(--backdrop-b));font-family:"Open Sans",sans-serif}
  .stage{position:absolute;left:0;top:0;width:1500px;height:1500px;transform:scale(.8);transform-origin:0 0}
  .page{position:absolute;width:702px;height:909px;overflow:hidden;box-shadow:0 6px 18px rgba(0,0,0,.35)}
  .abs{position:absolute}
  .photo{position:absolute;background:linear-gradient(160deg,var(--wood-a) 0%,#b48a5c 45%,var(--wood-b) 100%)}

  /* front */
  .front{left:38px;top:38px;background:var(--paper)}
  .front .shapes{position:absolute;left:0;top:0}
  .welcome{left:26px;top:335px;font-family:"Montserrat",sans-serif;font-weight:800;font-size:28px;color:var(--ink);letter-spacing:.5px}
  .headline{left:26px;top:370px;font-family:"Montserrat",sans-serif;font-weight:800;font-size:35px;line-height:43px;color:var(--red);letter-spacing:.5px}
  .tagline{left:26px;top:452px;font-size:18.5px;line-height:22px;color:var(--ink);letter-spacing:.3px}
  .brand{display:flex;align-items:center;gap:12px;font-family:"Montserrat",sans-serif;font-weight:600;letter-spacing:2.5px;line-height:1}
  .front .brand{left:448px;top:340px;color:var(--white);font-size:21px}
  .brand-mark{width:40px;height:40px;background:currentColor;flex:none}
  .about-kicker{left:419px;top:531px;font-family:"Montserrat",sans-serif;font-weight:800;font-size:21px;color:var(--red)}
  .about-title{left:417px;top:548px;font-family:"Montserrat",sans-serif;font-weight:800;font-size:41px;color:var(--red)}
  .facts{left:416px;top:603px;width:266px;list-style:none;font-size:14.5px;line-height:19.5px;color:var(--ink)}
  .facts li{position:relative;padding-left:15px;margin-bottom:3.5px}
  .facts li::before{content:"✓";position:absolute;left:0;top:0;color:var(--red);font-size:11px;font-weight:700}
  .facts li.sub{padding-left:35px}
  .facts li.sub::before{content:"➤";left:19px;font-size:10px}
  .front-footer{left:0;top:836px;height:73px;width:702px}
  .contact-line{position:absolute;display:flex;align-items:flex-start;gap:10px;font-family:"Montserrat",sans-serif;font-weight:700;font-size:12.5px;line-height:15.5px;color:var(--white);white-space:nowrap}

  /* back */
  .back{left:761px;top:543px;background:var(--white)}
  .force{left:0;top:0;width:408px;height:233px;background:var(--red)}
  .force-rule{position:absolute;left:25px;width:354px;height:5px;background:var(--white)}
  .force-title{position:absolute;left:0;top:33px;width:404px;text-align:center;font-family:"Montserrat",sans-serif;font-weight:800;font-size:32px;line-height:41px;color:var(--white);letter-spacing:.5px}
  .force-title span{color:var(--ink)}
  .force-copy{position:absolute;left:14px;top:134px;width:378px;text-align:center;font-size:14px;line-height:19.5px;color:var(--white);letter-spacing:-.1px}
  .plan{left:408px;top:0;width:294px;height:227px;background:var(--plan);border:1px solid #cfcfcf}
  .plan-rule{left:408px;top:227px;width:294px;height:6px;background:var(--red)}
  .more-title{left:28px;top:246px;font-family:"Montserrat",sans-serif;font-weight:800;font-size:21.5px;color:var(--red);letter-spacing:.2px}
  .back .brand{left:436px;top:260px;color:#4a4a4a;font-size:22px}
  .details{left:0;top:283px;width:408px;height:474px;background:var(--red);padding:26px 24px 0 24px}
  .details ul{list-style:none;color:var(--white);font-size:11px;line-height:14.4px}
  .details > ul > li{position:relative;padding-left:15px;margin-bottom:14px}
  .details > ul > li::before{content:"➤";position:absolute;left:0;top:0;font-size:9.5px}
  .details .tick{display:block;padding-left:6px}
  .details .tick::before{content:"✓ ";font-size:9px}
  .details em{font-weight:700}
  .contact-panel{left:408px;top:757px;width:294px;height:152px;background:var(--dark)}
  .contact-row{position:absolute;left:14px;display:flex;align-items:center;gap:14px;font-family:"Montserrat",sans-serif;font-weight:700;font-size:12.5px;line-height:15.5px;color:var(--white);white-space:nowrap}
  .icon-box{width:42px;height:36px;background:var(--red);display:flex;align-items:center;justify-content:center;flex:none}
</style>
</head>
<body>
<div class="stage">

  <!-- Front side -->
  <section class="page front">
    <svg class="shapes" width="702" height="909" viewBox="0 0 702 909">
      <polygon points="0,180 0,262 78,218" fill="var(--red)"/>
      <polygon points="702,88 702,560 367,382" fill="var(--red)"/>
      <polygon points="0,262 365,382 702,560 702,600 0,600" fill="#e9e9e9"/>
    </svg>
    <div class="photo" role="img" aria-label="Photo of the furnished executive office with conference table and arched window"
         style="left:0;top:0;width:702px;height:390px;clip-path:polygon(0 0,100% 0,100% 22.5%,52% 98%,0 67%)"></div>

    <div class="abs welcome">WELCOME TO</div>
    <div class="abs headline">THE CENTER OF<br>WHAT’S NEXT</div>
    <p class="abs tagline">This is where the power of real estate is<br>unleashed on your behalf.</p>

    <div class="abs brand"><span class="brand-mark"></span><span>HARWELL &amp;<br>STONE</span></div>

    <div class="photo" role="img" aria-label="Photo of a private office with desk and whiteboard" style="left:25px;top:522px;width:182px;height:128px"></div>
    <div class="photo" role="img" aria-label="Photo of an office desk by an arched window" style="left:223px;top:522px;width:182px;height:128px"></div>
    <div class="photo" role="img" aria-label="Photo of a smaller office with desk and framed print" style="left:25px;top:671px;width:182px;height:129px"></div>
    <div class="photo" role="img" aria-label="Photo of a corner office desk with window light" style="left:223px;top:671px;width:182px;height:129px"></div>

    <div class="abs about-kicker">ABOUT THE</div>
    <div class="abs about-title">PROPERTY</div>
    <ul class="abs facts">
      <li>Name of Building: Alder Road Centre</li>
      <li>Address: 4810 Alder Road, Palm Beach Gardens, FL 33418</li>
      <li>Building Size: 18,325 SF</li>
      <li>Vacant SF: 3,791 SF</li>
      <li>Occupancy: 79%</li>
      <li>Rental Rate: $32.00/SF plus suite electric</li>
      <li class="sub">No extra operating expenses.</li>
    </ul>

    <svg class="abs front-footer" width="702" height="73" viewBox="0 0 702 73">
      <polygon points="505,51 702,51 702,73 522,73" fill="var(--red)"/>
      <polygon points="0,0 472,0 522,73 0,73" fill="var(--dark)"/>
    </svg>
    <div class="contact-line" style="left:22px;top:859px">
      <svg width="12" height="16" viewBox="0 0 12 16"><path d="M6 0a6 6 0 0 0-6 6c0 4.5 6 10 6 10s6-5.5 6-10a6 6 0 0 0-6-6zm0 8.3A2.3 2.3 0 1 1 6 3.7a2.3 2.3 0 0 1 0 4.6z" fill="#fff"/></svg>
      <span>410 N Larkin 2200 Chicago, IL 60610<br>United States</span>
    </div>
    <div class="contact-line" style="left:336px;top:859px">
      <svg width="12" height="18" viewBox="0 0 12 18"><rect x="1" y="1" width="10" height="16" rx="2" fill="none" stroke="#fff" stroke-width="1.8"/><circle cx="6" cy="14" r="1" fill="#fff"/></svg>
      <span>(312) 555-0148</span>
    </div>
  </section>

  <!-- Back side -->
  <section class="page back">
    <div class="abs force">
      <div class="force-rule" style="top:25px"></div>
      <h2 class="force-title">WE ARE A FORCE<br><span>FOR ACTION</span></h2>
      <div class="force-rule" style="top:113px"></div>
      <p class="force-copy">Fueled by ideas, expertise and passion across borders and beyond service lines, we create real estate solutions to prepare our clients for what’s next.</p>
    </div>
    <div class="abs plan" role="img" aria-label="Floor plan of Suite 100 (top) and Suite 120 (bottom)"></div>
    <div class="abs plan-rule"></div>

    <h3 class="abs more-title">MORE ABOUT THE PROPERTY</h3>
    <div class="abs brand"><span class="brand-mark"></span><span>HARWELL &amp;<br>STONE</span></div>

    <div class="abs details">
      <ul>
        <li>Very easy to show as landlord is in the building. For leasing information, please contact:
          <span class="tick"><em><i>Dana Morel at 561-555-0192 or dana@morelgroup.com</i></em></span></li>
        <li>The Alder Road Centre is a beautiful Class A building situation in the heart of Palm Beach Gardens but without the crazy Harbor Blvd traffic.</li>
        <li>Alder Road Centre is located directly on I-95 just off of Alder Road. The massive, new Bayline development south entrance is being built across the street. The building is very convenient to restaurants, shopping, and every other trade needed.</li>
        <li>The suites are incredibly well appointed and move-in ready with custom oak doors and millwork, 10’ ceilings, floor to ceiling windows</li>
        <li>Two suites are available, which can be combined for 3,791 SF in total.
          <span class="tick">Suite 120 is available right now and is 1,488 SF with 1 large executive office, 2 smaller offices, a conference room, break room, and reception area.</span>
          <span class="tick">Suite 100 is available in February 2019, but could be vacated sooner. Suite 100 is 2,303 SF and has 6 offices, break room, reception area, and a very large meeting room.</span></li>
        <li>Features &amp; Amenities:
          <span class="tick">Plenty of parking</span>
          <span class="tick">On-site management</span>
          <span class="tick">Some furniture available if needed.</span></li>
      </ul>
    </div>

    <div class="photo" role="img" aria-label="Photo of the conference room with leather chairs and arched window" style="left:408px;top:341px;width:294px;height:416px"></div>
    <div class="photo" role="img" aria-label="Photo of an executive desk with file cabinets" style="left:0;top:757px;width:408px;height:152px"></div>

    <div class="abs contact-panel">
      <div class="contact-row" style="top:12px">
        <span class="icon-box"><svg width="14" height="19" viewBox="0 0 12 16"><path d="M6 0a6 6 0 0 0-6 6c0 4.5 6 10 6 10s6-5.5 6-10a6 6 0 0 0-6-6zm0 8.3A2.3 2.3 0 1 1 6 3.7a2.3 2.3 0 0 1 0 4.6z" fill="#fff"/></svg></span>
        <span>410 N Larkin 2200 Chicago,<br>IL 60610 United States</span>
      </div>
      <div class="contact-row" style="top:56px">
        <span class="icon-box"><svg width="13" height="20" viewBox="0 0 12 18"><rect x="1" y="1" width="10" height="16" rx="2" fill="none" stroke="#fff" stroke-width="1.8"/><circle cx="6" cy="14" r="1" fill="#fff"/></svg></span>
        <span>(312) 555-0148</span>
      </div>
      <div class="contact-row" style="top:101px">
        <span class="icon-box"><svg width="20" height="20" viewBox="0 0 20 20"><circle cx="10" cy="10" r="8.5" fill="none" stroke="#fff" stroke-width="1.8"/><path d="M1.5 10h17M10 1.5c3 3 3 14 0 17M10 1.5c-3 3-3 14 0 17" fill="none" stroke="#fff" stroke-width="1.5"/></svg></span>
        <span>www.harwellstone.com</span>
      </div>
    </div>
  </section>

</div>
</body>
</html>
```